New Template, new corporate image Kelvoran 2022

New template designs for google slides or PowerPoint. Match to new corporate image. The new website www.kelvoran-mx.example Needs to match our new version. Technology and Artificial Intelligence elements to reflect our type of work.
We are adding old version of template and will send elements for the new corporate images.
Please consider our website as the main corporate image.
Our templates are being used on customer presentations, webminars, internal work only.
We have our main name of company Kelvoran. Kelvoran has to be in all the templates.
Secondary logo or branded service is: Vastrelim.

Target Market(s)

Industrial users. Asset managers. Corporate visitors and customers.

Industry/Entity Type

Automotive. Chemical. Food and Beverage. Manufacturing

Other font styles liked:
• GE INSPIRA. RALEWAY

Colors
0054AA
0677BA
7BADD7
CADEEF
E8F1F8

Requirements
Must have
• Match to our elements on the new image. Use Brain Icons. Chips icons to connect equipments with software and control. Innovation.
Nice to have
• Unique images, machine images. Connecting machines and data elements. Template version for google slides. Image for industrial software for control equipment and saving money to manufacturers. Segments: Automotive, Chemical, Food and Beverages, Mining and pharmaceutical, Energy Management
Should not have
• old elements. not to much images of medical devices. Do not seems like a hospital.

```html
<!DOCTYPE html>
<html lang="en">
<head>
<meta charset="utf-8">
<title>Kelvoran Template 2022 – Part 2</title>
<link rel="stylesheet" href="https://fonts.googleapis.com/css2?family=Montserrat:wght@400;500;600;700;800;900&display=swap">
<style>
:root{
  --blue-900:#0054AA;
  --blue-700:#0677BA;
  --blue-400:#7BADD7;
  --blue-200:#CADEEF;
  --blue-050:#E8F1F8;
  --cyan:#12A3E8;
  --ink:#3a3a3a;
  --muted:#555;
  --page:#F0F1F3;
  --footer:#2B2B2B;
  --card:#EFEFEF;
  --row:#F2F2F2;
}
*{box-sizing:border-box;margin:0;padding:0}
html,body{width:1200px;height:1200px;overflow:hidden}
body{background:var(--page);font-family:'Montserrat',sans-serif;color:var(--ink);position:relative}
.slide{position:absolute;width:543px;height:305px;background:#fff;overflow:hidden}
.s-team{left:41px;top:41px}
.s-break{left:614px;top:41px;background:#000}
.s-chart{left:41px;top:370px}
.s-services{left:614px;top:370px}
.s-table{left:41px;top:702px}
.s-map{left:614px;top:702px}
.abs{position:absolute}
.slide-title{position:absolute;left:22px;top:24px;font-size:19.5px;font-weight:700;color:var(--blue-900);letter-spacing:.2px}
.footer{position:absolute;left:0;bottom:0;width:100%;height:22px;background:var(--footer);display:flex;align-items:center;padding:0 22px;font-size:5.6px;color:#ddd}
.footer .page-no{color:var(--cyan);font-weight:600;margin-right:5px;min-width:3px}
.footer .sep{margin-right:6px}
.footer .brand{margin-left:auto;font-size:6.5px;font-weight:600;color:var(--blue-400);letter-spacing:.4px}
/* team */
.member{position:absolute;top:66px;width:155px;text-align:center}
.member .photo{width:155px;height:157px}
.member .bar{height:3px;background:linear-gradient(90deg,var(--blue-900),var(--cyan))}
.member .name{margin-top:10px;font-size:10px;font-weight:700;color:var(--blue-900)}
.member .role{font-size:8.5px;color:var(--muted);margin-top:1px}
/* break */
.plasma{position:absolute;left:0;top:0;width:330px;height:305px;background:radial-gradient(circle at 90px 110px,#9cc9ff 0,#3c77b8 6%,#16335a 22%,#0a1626 45%,#000 70%)}
.break-title{position:absolute;right:26px;top:110px;font-size:38px;font-weight:800;color:var(--cyan)}
.break-rule{position:absolute;right:27px;top:165px;width:47px;height:2px;background:#fff}
.break-sub{position:absolute;right:26px;top:179px;font-size:8.5px;color:#fff}
/* chart */
.sec{position:absolute;left:23px;width:230px}
.sec h3{font-size:12px;font-weight:700;color:var(--blue-900);margin-bottom:3px}
.sec p{font-size:8.5px;line-height:10.8px;color:var(--muted)}
.hr{position:absolute;left:23px;top:156px;width:230px;height:1px;background:#ccc}
.vr{position:absolute;left:285px;top:63px;width:1px;height:205px;background:#ddd}
.chart-label{position:absolute;left:340px;width:130px;top:67px;text-align:center;font-size:10px;font-weight:700;color:var(--blue-900)}
.legend{position:absolute;left:325px;top:246px;font-size:7.5px;color:#666;display:flex;gap:8px}
.legend i{display:inline-block;width:4px;height:4px;margin-right:2px;vertical-align:1px}
/* services */
.svc{position:absolute;top:64px;width:122px;height:160px;background:var(--card);text-align:center}
.svc .icon{position:absolute;left:39px;top:16px;width:44px;height:44px;border-radius:50%;background:radial-gradient(circle at 35% 30%,var(--cyan),var(--blue-900))}
.svc .icon svg{position:absolute;left:10px;top:10px;width:24px;height:24px}
.svc .line{position:absolute;left:10px;right:10px;top:73px;height:1px;background:var(--blue-400)}
.svc h3{position:absolute;top:84px;width:100%;font-size:11.5px;font-weight:700;color:var(--blue-900)}
.svc p{position:absolute;top:101px;left:12px;right:12px;font-size:8px;line-height:9.4px;color:var(--muted)}
.svc-foot{position:absolute;left:30px;right:30px;top:236px;text-align:center;font-size:8.8px;line-height:11px;color:var(--muted)}
/* table */
.data-table{position:absolute;left:22px;top:60px;width:500px;border-collapse:collapse;table-layout:fixed;border-bottom:1.5px solid var(--blue-900)}
.data-table th{background:var(--blue-900);color:#fff;font-size:10.5px;font-weight:700;text-align:left;height:31px;padding-left:4px}
.data-table td{height:32px;padding-left:4px;font-size:10px;color:#444}
.data-table td:first-child{color:var(--blue-900);font-weight:700;font-size:11px}
.data-table tr:nth-child(even) td{background:var(--row)}
/* map */
.world{position:absolute;left:85px;top:61px;width:340px;height:196px;background:radial-gradient(ellipse at center,#ebebeb 0,#f2f2f2 60%,#fff 100%);border-radius:40px}
.pin{position:absolute;width:21px;height:21px;margin:-10.5px 0 0 -10.5px;border-radius:50%;background:radial-gradient(circle at 35% 30%,var(--cyan),var(--blue-900));color:#fff;font-size:7px;font-weight:700;display:flex;align-items:center;justify-content:center}
.pin-note{position:absolute;font-size:7px}
.pin-note b{display:block;color:var(--blue-900);font-weight:700}
.pin-note span{font-size:5.4px;color:#666}
.pin-note.r{text-align:right}
.part{position:absolute;left:44px;top:1060px;font-size:108px;font-weight:900;color:#000;letter-spacing:2px;line-height:1}
</style>
</head>
<body>

<section class="slide s-team">
  <h2 class="slide-title">Meet Our Team</h2>
  <div class="member" style="left:22px">
    <div class="photo" role="img" aria-label="Portrait photo of a team member" style="background:linear-gradient(160deg,#8aa84a,#c9b48f 60%,#e9e4dc)"></div>
    <div class="bar"></div>
    <div class="name">Enter Name Here</div><div class="role">Subtitle</div>
  </div>
  <div class="member" style="left:194px">
    <div class="photo" role="img" aria-label="Portrait photo of a team member" style="background:linear-gradient(160deg,#cfd3d8,#b9bec4 55%,#dfe3e8)"></div>
    <div class="bar"></div>
    <div class="name">Enter Name Here</div><div class="role">Subtitle</div>
  </div>
  <div class="member" style="left:366px">
    <div class="photo" role="img" aria-label="Portrait photo of a team member" style="background:linear-gradient(180deg,#c9cdd3,#b79a86 55%,#5a6fd0)"></div>
    <div class="bar"></div>
    <div class="name">Enter Name Here</div><div class="role">Subtitle</div>
  </div>
  <footer class="footer"><span class="page-no">8</span><span class="sep">|</span>Copyright © Kelvoran 2022<span class="brand">kelvoran</span></footer>
</section>

<section class="slide s-break">
  <div class="plasma" role="img" aria-label="Blue plasma light filaments on black"></div>
  <h2 class="break-title">Break Slide</h2>
  <div class="break-rule"></div>
  <p class="break-sub">Lorem ipsum dolor sit amet, consectetur.</p>
</section>

<section class="slide s-chart">
  <h2 class="slide-title">Chart with Content</h2>
  <div class="sec" style="top:73px">
    <h3>Section Header</h3>
    <p>Donec vel suscipit purus, ultrices ornare neque. Sed nec est a lacus lacinia venenatis non at est. Vestibulum vitae lorem lectus. Phasellus gravida mauris a sapien elementum malesuada. Vestibulum ut urna eu dolor.</p>
  </div>
  <div class="hr"></div>
  <div class="sec" style="top:172px">
    <h3>Section Header</h3>
    <p>Lorem ipsum dolor sit amet, consectetur adipiscing elit. Curabitur at fringilla velit. In ac sagittis nulla. Nulla quis erat et ligula aliquam sagittis in viverra mauris. Pellentesque a hendrerit orci at.</p>
  </div>
  <div class="vr"></div>
  <div class="chart-label">Sales</div>
  <svg class="abs" style="left:329px;top:86px" width="152" height="152" viewBox="0 0 152 152" role="img" aria-label="Donut chart of quarterly sales">
    <g transform="rotate(-90 76 76)" fill="none" stroke-width="23">
      <circle cx="76" cy="76" r="64.5" stroke="#0054AA" stroke-dasharray="234 405.3"/>
      <circle cx="76" cy="76" r="64.5" stroke="#0677BA" stroke-dasharray="101 405.3" stroke-dashoffset="-235"/>
      <circle cx="76" cy="76" r="64.5" stroke="#7BADD7" stroke-dasharray="36 405.3" stroke-dashoffset="-337"/>
      <circle cx="76" cy="76" r="64.5" stroke="#CADEEF" stroke-dasharray="31 405.3" stroke-dashoffset="-374"/>
    </g>
  </svg>
  <div class="legend">
    <span><i style="background:#0054AA"></i>1st Qtr</span>
    <span><i style="background:#0677BA"></i>2nd Qtr</span>
    <span><i style="background:#7BADD7"></i>3rd Qtr</span>
    <span><i style="background:#CADEEF"></i>4th Qtr</span>
  </div>
  <footer class="footer"><span class="page-no">9</span><span class="sep">|</span>Copyright © Kelvoran 2022<span class="brand">kelvoran</span></footer>
</section>

<section class="slide s-services">
  <h2 class="slide-title">Services</h2>
  <div class="svc" style="left:17px">
    <div class="icon"><svg viewBox="0 0 24 24" fill="none" stroke="#fff" stroke-width="1.5"><circle cx="12" cy="12" r="3"/><circle cx="5" cy="5" r="2.5"/><circle cx="19" cy="5" r="2.5"/><circle cx="5" cy="19" r="2.5"/><circle cx="19" cy="19" r="2.5"/><path d="M7 7l3 3M17 7l-3 3M7 17l3-3M17 17l-3-3"/></svg></div>
    <div class="line"></div><h3>Section Header</h3>
    <p>Lorem ipsum dolor sit amet, consecteturat es adipiscing elit. Curabitur fringilla</p>
  </div>
  <div class="svc" style="left:144px">
    <div class="icon"><svg viewBox="0 0 24 24" fill="none" stroke="#fff" stroke-width="1.5"><rect x="5" y="6" width="14" height="10" rx="2"/><circle cx="9.5" cy="11" r="1.3"/><circle cx="14.5" cy="11" r="1.3"/><path d="M12 6V3M3 10v3M21 10v3M9 16v4M15 16v4M12 16v5"/></svg></div>
    <div class="line"></div><h3>Section Header</h3>
    <p>Lorem ipsum dolor sit amet, consecteturat es adipiscing elit. Curabitur fringilla</p>
  </div>
  <div class="svc" style="left:271px">
    <div class="icon"><svg viewBox="0 0 24 24" fill="none" stroke="#fff" stroke-width="1.6" stroke-linejoin="round"><path d="M14 2L6 13h5l-2 9 9-12h-5l2-8z"/></svg></div>
    <div class="line"></div><h3>Section Header</h3>
    <p>Lorem ipsum dolor sit amet, consecteturat es adipiscing elit. Curabitur fringilla</p>
  </div>
  <div class="svc" style="left:399px">
    <div class="icon"><svg viewBox="0 0 24 24" fill="none" stroke="#fff" stroke-width="1.5"><rect x="6" y="6" width="12" height="16" rx="1"/><path d="M8 6V3h8v3"/><circle cx="11" cy="15" r="1.8" fill="#fff"/><path d="M14 10v9"/></svg></div>
    <div class="line"></div><h3>Section Header</h3>
    <p>Lorem ipsum dolor sit amet, consecteturat es adipiscing elit. Curabitur fringilla</p>
  </div>
  <p class="svc-foot">Lorem ipsum dolor sit amet, consectetur adipiscing elit. Curabitur at fringilla velit. In ac sagittis nulla. Nulla quis erat et ligula aliquam sagittis in viverra mauris. Pellentesque pharetra hendrerit orci at.</p>
  <footer class="footer"><span class="page-no">10</span><span class="sep">|</span>Copyright © Kelvoran 2022<span class="brand">kelvoran</span></footer>
</section>

<section class="slide s-table">
  <h2 class="slide-title">Table Slides</h2>
  <table class="data-table">
    <thead><tr><th>Data</th><th>Header</th><th>Header</th><th>Header</th><th>Header</th><th>Header</th><th>Header</th><th>Header</th></tr></thead>
    <tbody>
      <tr><td>Value</td><td>00</td><td>00</td><td>00</td><td>00</td><td>00</td><td>00</td><td>00</td></tr>
      <tr><td>Value</td><td>00</td><td>00</td><td>00</td><td>00</td><td>00</td><td>00</td><td>00</td></tr>
      <tr><td>Value</td><td>00</td><td>00</td><td>00</td><td>00</td><td>00</td><td>00</td><td>00</td></tr>
      <tr><td>Value</td><td>00</td><td>00</td><td>00</td><td>00</td><td>00</td><td>00</td><td>00</td></tr>
      <tr><td>Value</td><td>00</td><td>00</td><td>00</td><td>00</td><td>00</td><td>00</td><td>00</td></tr>
    </tbody>
  </table>
  <footer class="footer"><span class="page-no"></span><span class="sep">|</span>Copyright © Kelvoran 2022<span class="brand">kelvoran</span></footer>
</section>

<section class="slide s-map">
  <h2 class="slide-title">Map Slide</h2>
  <div class="world" role="img" aria-label="Light grey world map"></div>
  <div class="pin" style="left:142px;top:144px">01</div>
  <div class="pin" style="left:389px;top:117px">02</div>
  <div class="pin" style="left:272px;top:119px">03</div>
  <div class="pin" style="left:404px;top:227px">04</div>
  <div class="pin" style="left:264px;top:174px">05</div>
  <div class="pin" style="left:197px;top:207px">06</div>
  <div class="pin-note r" style="right:422px;top:136px"><b>Section Header</b><span>Lorem ipsum dolor sit amet.</span></div>
  <div class="pin-note" style="left:261px;top:86px"><b>Section Header</b><span>Lorem ipsum dolor sit amet.</span></div>
  <div class="pin-note" style="left:409px;top:107px"><b>Section Header</b><span>Lorem ipsum dolor sit amet.</span></div>
  <div class="pin-note" style="left:283px;top:164px"><b>Section Header</b><span>Lorem ipsum dolor sit amet.</span></div>
  <div class="pin-note r" style="right:368px;top:197px"><b>Section Header</b><span>Lorem ipsum dolor sit amet.</span></div>
  <div class="pin-note" style="left:423px;top:217px"><b>Section Header</b><span>Lorem ipsum dolor sit amet.</span></div>
  <footer class="footer"><span class="page-no"></span><span class="sep">|</span>Copyright © Kelvoran 2022<span class="brand">kelvoran</span></footer>
</section>

<div class="part">PART 2</div>

</body>
</html>
```